PITCH PRESENTATION for Feature Film Project

A while ago I had some key art designed for me for a film project called Lanternfall's Promise (I see it's still in the online portfolio for pixelharbor, who did the original work). I'm now taking that project to a series of pitch meetings at a film festival here in Canada and am putting together a powerpoint presentation.
I would want you to use the original design/aesthetic framework across the 14 pages of the presentation. I have provided the text and some image ideas (there's also one video to insert) that you may or may not use, etc. Probably for a large chunk of the pages - perhaps 6 of the ten - you could just clean it up and create a common background theme on which to place the companion text. Obviously, while making it pretty is a priority, it's also a priority for it to be legible to the people whom I'm pitching the project when it is projected onto a large screen.
I've uploaded a draft of the powerpoint text - there could be some minor changes between now and next week. I'll be leaving for the festival on December 3 so, obviously need a final version before that date. I've attached a .jpg of the original artwork along with the powerpoint.

Let me know if you need more details.
Updates

I wasn't able to upload the .psd file of the original poster artwork with layers & fonts but here is a link to download it from my filecrate: https://www.filecrate.example/s/k4p8tq2rnx7vb3m/FA-Lanternfall%27s%20Promise%20poster.psd?dl=0 best Gareth

Target Market(s)

This is targeted at some Chinese studio executives to whom the project will be pitched. It is for a film that is a martial arts thriller.

Industry/Entity Type

Festival

Requirements
Must have
• The main thing is to use the already-existing material (the poster - incl colour scheme and fonts) as the aesthetic foundation for the presentation. We are, in a sense, trying to strengthen the brand identity of the project with the execs.

```html
<!DOCTYPE html>
<html lang="en">
<head>
<meta charset="utf-8">
<title>Reelvance – Pitch Slides</title>
<link rel="stylesheet" href="https://fonts.googleapis.com/css2?family=Carlito:wght@400;700&family=Tinos&display=swap">
<style>
  :root{
    --backdrop:#ece6da;
    --paper-light:#ead3a0;
    --paper-mid:#dfc188;
    --paper-dark:#cfa96c;
    --banner:#c4573a;
    --tab:#c8374a;
    --ink:#1d1a14;
    --arrow:#e07b28;
    --white:#ffffff;
  }
  *{margin:0;padding:0;box-sizing:border-box}
  html,body{width:1200px;height:1000px;overflow:hidden;background:var(--backdrop)}
  .canvas{position:relative;width:1200px;height:1000px}
  .slide{
    position:absolute;width:722px;height:540px;overflow:hidden;
    background:
      radial-gradient(ellipse at 30% 70%, rgba(200,120,80,.18), transparent 55%),
      radial-gradient(ellipse at 80% 20%, rgba(255,240,200,.35), transparent 60%),
      linear-gradient(135deg,var(--paper-light),var(--paper-mid) 55%,var(--paper-dark));
    box-shadow:0 4px 14px rgba(0,0,0,.35);
    font-family:"Carlito","Calibri",sans-serif;color:var(--ink);
  }
  .slide--company{left:12px;top:0;height:540px;width:720px}
  .slide--studio{left:468px;top:440px}
  .banner{position:absolute;left:0;width:100%;height:100px}
  .banner svg{position:absolute;inset:0;width:100%;height:100%}
  .banner-title{
    position:absolute;inset:0;display:flex;align-items:center;justify-content:center;
    font-family:"Tinos","Times New Roman",serif;font-size:44px;color:var(--white);letter-spacing:1px;
  }
  .tab{position:absolute;left:0;height:60px}
  .tab svg{position:absolute;inset:0;width:100%;height:100%}
  .tab-label{position:absolute;left:44px;top:0;height:100%;display:flex;align-items:center;color:var(--white)}
  .copy{position:absolute;font-size:15.5px;line-height:22px}
  .copy p{margin-bottom:0}
  .bullets{list-style:none}
  .bullets li{position:relative;padding-left:32px}
  .bullets li::before{
    content:"";position:absolute;left:0;top:6px;
    border-left:11px solid var(--arrow);border-top:6px solid transparent;border-bottom:6px solid transparent;
  }
  .small{font-size:12.5px;line-height:19.5px}
  .credits{font-size:13px;line-height:18px}
</style>
</head>
<body>
<div class="canvas">

  <!-- Company overview slide -->
  <section class="slide slide--company">
    <div class="banner" style="top:10px">
      <svg viewBox="0 0 720 100" preserveAspectRatio="none" aria-hidden="true">
        <polygon fill="#fff" points="0,2 40,0 90,3 150,0 210,2 280,0 340,3 400,1 470,2 540,0 610,3 670,1 720,2 720,98 660,100 600,96 530,99 460,97 390,100 320,96 250,99 180,96 110,99 50,97 0,99"/>
        <polygon fill="var(--banner)" points="0,5 60,4 120,6 190,3 260,6 330,4 400,6 470,3 540,6 610,4 680,6 720,4 720,92 650,94 580,91 510,95 440,92 370,95 300,91 230,94 160,91 90,95 30,92 0,94"/>
      </svg>
      <div class="banner-title">REELVANCE</div>
    </div>

    <div class="copy" style="left:44px;top:131px;width:650px">
      <p><b>Reelvance</b> was founded in 2000 by Elodie Fournel.</p>
      <p style="margin-top:1px">It has two distinct but complementary units: <b>Production and Financing.</b></p>
      <p style="margin-top:4px">Its access to reliable sources of capital means it can accelerate execution of projects for the international market.</p>
    </div>

    <div class="tab" style="top:238px;width:268px">
      <svg viewBox="0 0 268 60" preserveAspectRatio="none" aria-hidden="true">
        <polygon fill="#fff" points="0,0 60,2 130,0 200,2 266,0 268,60 200,58 130,60 60,58 0,60"/>
        <polygon fill="var(--tab)" points="0,4 70,5 140,3 210,5 264,4 262,30 265,56 200,55 130,57 60,55 0,56"/>
      </svg>
      <div class="tab-label" style="font-size:24px;font-weight:700">Financial Division</div>
    </div>

    <div class="copy" style="left:43px;top:307px;width:660px">
      <p>Reelvance has raised two funds: <b>Reelvance Capital</b> and <b>Reelvance Investment.</b></p>
      <p><b>Reelvance Capital</b> supports Reelvance’ production division and its strategic partners by providing:</p>
    </div>

    <ul class="copy bullets" style="left:43px;top:392px;width:240px;font-weight:700;line-height:21px">
      <li style="top:2px">Gap financing</li>
      <li>Bridge financing</li>
    </ul>
    <ul class="copy bullets" style="left:298px;top:387px;width:400px;font-weight:700;line-height:21px">
      <li>Presales financing</li>
      <li>Government tax credit and subsidies financing</li>
    </ul>

    <div class="copy" style="left:43px;top:459px;width:660px">
      <p>As added value to Reelvance Capital’s debt product, <b>Reelvance Investment</b> is an equity fund which will co-invest on a pro-rata participation basis with the lender on a project.</p>
    </div>
  </section>

  <!-- Studio slide -->
  <section class="slide slide--studio">
    <div class="banner" style="top:14px;height:98px">
      <svg viewBox="0 0 720 100" preserveAspectRatio="none" aria-hidden="true">
        <polygon fill="#fff" points="0,2 40,0 90,3 150,0 210,2 280,0 340,3 400,1 470,2 540,0 610,3 670,1 720,2 720,98 660,100 600,96 530,99 460,97 390,100 320,96 250,99 180,96 110,99 50,97 0,99"/>
        <polygon fill="var(--banner)" points="0,5 60,4 120,6 190,3 260,6 330,4 400,6 470,3 540,6 610,4 680,6 720,4 720,92 650,94 580,91 510,95 440,92 370,95 300,91 230,94 160,91 90,95 30,92 0,94"/>
      </svg>
      <div class="banner-title">REELMAX</div>
    </div>

    <div class="copy small" style="left:51px;top:130px;width:650px">
      <p><b>Reelvance’</b> award-winning production division, founded in 2009 with support from a billion dollar pension fund.</p>
      <p>Our model:</p>
    </div>
    <ul class="copy small bullets" style="left:51px;top:169px;width:630px">
      <li>Experienced development team</li>
      <li style="margin-top:1px">Experienced production team</li>
      <li style="margin-top:1px">Leverage our substantial and stable access to capital and our long-standing relationships with international sales agents, distributors and broadcasters.</li>
    </ul>

    <div class="tab" style="top:256px;width:307px;height:52px">
      <svg viewBox="0 0 307 52" preserveAspectRatio="none" aria-hidden="true">
        <polygon fill="#fff" points="0,0 70,2 150,0 230,2 305,0 307,52 230,50 150,52 70,50 0,52"/>
        <polygon fill="var(--tab)" points="0,4 80,5 160,3 240,5 303,4 301,26 304,48 230,47 150,49 70,47 0,48"/>
      </svg>
      <div class="tab-label" style="left:48px;font-size:25px">Recent Productions</div>
    </div>

    <div class="copy credits" style="left:49px;top:328px;width:650px">
      <p><b>Polar Hours</b> (feature) – Producer, Reelmax (Montreal)/Vero Lume SRL (Italy), $17M</p>
      <p><b>Exile Road</b> (feature) - Producer, Reelmax (Montreal)/Jadepeak Film Group (China)/Minuit Vingt (France), $25M</p>
      <p><b>Nalua</b> (feature) - Producer, Reelmax (Montreal)/Productions Calliope (Québec)/Aube Claire (Montreal), $9.5M</p>
      <p><b>Turbo Dash</b> (animated series) - Executive Producer, Reelvance International/Reelmax (Montreal)/ Inkwave (Singapore), $6.9M</p>
      <p><b>Spells Without Words</b> (TV movie) - Producer, Reelmax (Montreal)/Hearthside (USA), $3.8M US</p>
      <p><b>The Lantern Journals</b> (feature) - Producer, Reelmax (Montreal)/Corrib Pictures (Ireland), $12M</p>
    </div>
  </section>

</div>
</body>
</html>
```